International Woodworking Brand needs new site

Our Website has not been revamped for a long time.. The imaging and construction are now tired and dated. Its clumsy and cumbersome to edit, uses outdated software. The site can only be edited and updated from NZ. We need multiple editors worldwide refreshing our content, within prescribed templates to maintain look and feel. We want to use a Wordpress platform.

KELBRO is the main brand of the Forvane Industries. Traditionally, the website is branded with Forvane, the company name. This is incorrect now and needs a shift to our KELBRO brand. Also new levels of service and functionality are required.

KELBRO has a strong reputation in the market place for innovation and leading edge technology in it's field. We have also worked hard to develop a reputation for excellent customer service. Our website also needs to reflect and reinforce these concepts.

We want a fresh, clean, modern site that meets all best practices of SEO marketing, is easy for our customers to navigate and use, and reinforces our brand reputation and our product sales.

See the attached Brief for more specifics.

Target Market(s)

End Users - Woodworkers
Dealers/Stores
Forvane Employees

More demographic and customer profile info is available on request

Industry/Entity Type

Woodworking

Coding

Coded - Design and coding required

Font styles to use
Sans Serif

Colors
ec1f27

Requirements
Must have
• See the brief attached
Nice to have
• See the brief attached
Should not have
• See the brief attached

```html
<!DOCTYPE html>
<html lang="en">
<head>
<meta charset="utf-8">
<title>KELBRO</title>
<link href="https://fonts.googleapis.com/css2?family=Open+Sans:wght@400;600;700&family=Oswald:wght@300;400;500&display=swap" rel="stylesheet">
<style>
:root{
  --red:#ec1f27;
  --red-dark:#c9161d;
  --page:#343434;
  --footer:#2c2c2c;
  --footer-base:#232323;
  --ink:#333;
  --light:#f2f2f2;
  --line:#cfcfcf;
  --footer-text:#a9a9a9;
  --footer-head:#e8484e;
}
*{box-sizing:border-box;margin:0;padding:0}
html,body{width:822px;height:1200px;overflow:hidden}
body{background:var(--page);font-family:"Open Sans",Arial,sans-serif;color:var(--ink);position:relative}
.site{position:absolute;left:90px;top:0;width:641px;height:1041px;background:#fff}
.header{height:60px;position:relative}
.brand{position:absolute;left:8px;top:19px;display:flex;align-items:center;gap:6px;font-family:"Oswald",sans-serif;font-weight:500;font-size:18px;color:var(--red);letter-spacing:.5px}
.brand-dot{width:12px;height:12px;border-radius:50%;background:var(--red)}
.lang{position:absolute;left:416px;top:18px;width:72px;height:25px;border:1px solid #ddd;display:flex;align-items:center;padding-left:7px;font-size:8px;color:#555;gap:5px}
.lang-flag{width:11px;height:7px;background:#b7c0d8}
.lang svg{position:absolute;right:7px;top:10px}
.search{position:absolute;left:496px;top:18px;width:138px;height:25px;border:1px solid #ddd;font-size:8px;color:#888;padding:8px 0 0 10px}
.search svg{position:absolute;right:8px;top:7px}
.nav{height:27px;background:var(--red);display:flex;font-size:7.5px;font-weight:600;color:#fff;text-transform:uppercase}
.nav a{color:#fff;text-decoration:none;display:flex;align-items:center;justify-content:center}
.nav .active{background:var(--red-dark)}
.hero{position:relative;height:231px;background:radial-gradient(ellipse at 75% 40%,#7d8088 0%,#3b3e46 30%,#0b0c16 62%,#05050d 100%)}
.hero h1{position:absolute;left:24px;top:70px;font-family:"Oswald",sans-serif;font-weight:400;font-size:21px;line-height:26px;color:#b9b9bd;letter-spacing:-.2px}
.btn-red{position:absolute;left:24px;top:131px;height:26px;padding:0 8px;background:var(--red);color:#fff;font-family:"Oswald",sans-serif;font-size:11px;display:flex;align-items:center}
.dots{position:absolute;left:292px;top:205px;display:flex;gap:8px}
.dots span{width:9px;height:9px;border:1.2px solid #ddd;border-radius:50%}
.dots .on{background:radial-gradient(circle,#fff 35%,transparent 40%)}
.cats{position:absolute;left:9px;top:328px;display:grid;grid-template-columns:repeat(3,203px);gap:8px 8px}
.cat{height:131px;position:relative}
.cat-label{position:absolute;left:0;right:0;bottom:0;height:27px;background:rgba(236,31,39,.88);color:#fff;font-family:"Oswald",sans-serif;font-size:12.5px;display:flex;align-items:center;justify-content:center}
.about-title{position:absolute;left:9px;top:622px;width:623px;display:flex;align-items:center;gap:14px;font-family:"Oswald",sans-serif;font-weight:400;font-size:25px;color:#222}
.about-title::before,.about-title::after{content:"";flex:1;height:1px;background:var(--line)}
.about-text{position:absolute;left:10px;top:657px;width:621px;font-size:7px;line-height:13px;color:#666;text-align:center}
.partner{position:absolute;left:0;width:641px;top:716px;text-align:center;font-family:"Oswald",sans-serif;font-weight:500;font-size:20px;color:#9a9a9a;letter-spacing:1px}
.promo{position:absolute;top:770px;width:306px;height:110px;border:1px solid #e3e3e3;background:linear-gradient(90deg,#fff,#f4f4f4)}
.promo-img{position:absolute;left:18px;top:6px;width:135px;height:98px}
.promo p{position:absolute;right:18px;top:28px;text-align:right;font-family:"Oswald",sans-serif;font-weight:300;font-size:12px;line-height:16px;color:#555}
.btn-dark{position:absolute;right:18px;top:66px;height:25px;padding:0 9px;background:#333;color:#fff;font-family:"Oswald",sans-serif;font-size:9.5px;display:flex;align-items:center}
.news-title{position:absolute;left:10px;top:902px;font-family:"Oswald",sans-serif;font-weight:400;font-size:23px;color:#222}
.pager{position:absolute;left:596px;top:906px;display:flex;gap:3px}
.pager span{width:17px;height:20px;border:1px solid #ddd;display:flex;align-items:center;justify-content:center}
.news{position:absolute;left:9px;top:937px;display:grid;grid-template-columns:repeat(3,203px);gap:8px}
.card{height:92px;background:var(--light);border-top:2px solid #222;position:relative}
.date{position:absolute;left:9px;top:12px;font-size:7px;color:#333;text-align:center;line-height:12px}
.date b{display:block;font-weight:400;font-size:12px}
.card h3{position:absolute;left:35px;top:11px;width:150px;font-weight:400;font-size:8px;line-height:12px;color:var(--red)}
.card p{position:absolute;left:35px;top:40px;width:160px;font-size:5.6px;line-height:10px;color:#8a8a8a;text-align:justify}
.footer{position:absolute;left:0;top:1041px;width:822px;height:121px;background:var(--footer)}
.fcol{position:absolute;top:28px}
.fcol h4{font-weight:400;font-size:9px;color:var(--footer-head);margin-bottom:7px}
.fcol ul{list-style:none;font-size:6.6px;line-height:13.2px;color:var(--footer-text)}
.fcol li::before{content:"•";margin-right:5px}
.fcol.support ul{line-height:15.5px}
.vline{position:absolute;top:23px;width:1px;height:78px;background:#444}
.subscribe{display:flex;width:151px;height:25px}
.subscribe span{flex:1;background:#fff;font-size:6.8px;color:#666;padding:8px 0 0 9px}
.subscribe b{width:18px;background:var(--red);display:flex;align-items:center;justify-content:center}
.social{display:grid;grid-template-columns:repeat(3,16px);gap:5px 6px}
.social span{width:16px;height:16px;border-radius:50%}
.bottom{position:absolute;left:0;top:1162px;width:822px;height:38px;background:var(--footer-base);text-align:center;font-size:7px;color:#aaa;padding-top:17px}
</style>
</head>
<body>
<div class="site">
  <header class="header">
    <div class="brand"><span class="brand-dot"></span>KELBRO</div>
    <div class="lang"><span class="lang-flag"></span>English
      <svg width="7" height="4" viewBox="0 0 7 4"><path d="M0 0h7L3.5 4z" fill="#333"/></svg></div>
    <div class="search">Search
      <svg width="10" height="10" viewBox="0 0 10 10"><circle cx="4" cy="4" r="3.2" fill="none" stroke="#222" stroke-width="1.4"/><path d="M6.4 6.4 9.3 9.3" stroke="#222" stroke-width="1.5"/></svg></div>
  </header>
  <nav class="nav">
    <a class="active" style="width:69px">Home</a>
    <a style="width:65px">Products</a>
    <a style="width:79px">Support</a>
    <a style="width:89px">Where to buy</a>
    <a style="width:128px">Register your warranty</a>
    <a style="width:80px">About</a>
    <a style="width:80px">Contact</a>
  </nav>
  <section class="hero" role="img" aria-label="Close-up of a milling cutter machining a metal plate">
    <h1>Donec vitae dolor blandit<br>tincidunt tortor</h1>
    <div class="btn-red">Learn more</div>
    <div class="dots"><span class="on"></span><span></span><span></span><span></span></div>
  </section>

  <section class="cats">
    <div class="cat" role="img" aria-label="Lathe turning a metal part" style="background:linear-gradient(135deg,#2b2d31,#8b8e94 55%,#3a3b3f)"><div class="cat-label">LATHES</div></div>
    <div class="cat" role="img" aria-label="Machined metal flanges" style="background:linear-gradient(135deg,#d9d9d9,#8c8c8c 50%,#c8c8c8)"><div class="cat-label">LATHE ACCESSORIES</div></div>
    <div class="cat" role="img" aria-label="Lathe chuck with jaws" style="background:linear-gradient(135deg,#3d8fb0,#9fb9c6 50%,#56a6c6)"><div class="cat-label">CHUCKS</div></div>
    <div class="cat" role="img" aria-label="Precision chuck parts on a workbench" style="background:linear-gradient(135deg,#cfd2d6,#8f98a8 55%,#3f4f88)"><div class="cat-label">CHUCK ACCESSORIES</div></div>
    <div class="cat" role="img" aria-label="Large industrial workshop hall" style="background:linear-gradient(180deg,#3c5f9e,#c9c6b6 55%,#8a8a80)"><div class="cat-label">WORKSHOP</div></div>
    <div class="cat" role="img" aria-label="Assorted steel tubes and bearings" style="background:linear-gradient(135deg,#5a5a5a,#cfcfcf 45%,#2e2e2e)"><div class="cat-label">OTHER</div></div>
  </section>

  <h2 class="about-title">ABOUT KELBRO</h2>
  <p class="about-text">Aliquam scelerisque enim ipsum, sit amet convallis orci dapibus non. Donec purus diam, maximus quis pulvinar eu, semper ac augue. Aenean tempus iaculis urna. Pellentesque habitant morbi tristique senectus et netus et malesuada fames ac turpis egestas. Pellentesque tincidunt neque vel tellus suscipit, at pulvinar neque volutpat. Morbi ut leo ut ex porta rhoncus iaculis at erat. Vestibulum imperdiet elit nec nulla dignissim, sit amet condimentum elit malesuada. Suspendisse vehicula, justo in mollis vulputate, nisi massa rhoncus dolor, eu sollicitudin mi eros sit amet metus. Ut accumsan vehicula posuere.</p>
  <div class="partner">KELBRO</div>

  <div class="promo" style="left:10px">
    <div class="promo-img" role="img" aria-label="Pair of wheel spacers with bolts" style="background:radial-gradient(ellipse,#9a9a9a,#e6e6e6 70%,transparent 72%)"></div>
    <p>Morbi ut leo ut ex<br>porta rhoncus iaculis at erat</p>
    <div class="btn-dark">Read more</div>
  </div>
  <div class="promo" style="left:328px">
    <div class="promo-img" role="img" aria-label="Bundle of twist drill bits" style="background:radial-gradient(ellipse,#6f6f6f,#d8d8d8 65%,transparent 70%)"></div>
    <p>Morbi ut leo ut ex<br>porta rhoncus iaculis at erat</p>
    <div class="btn-dark">Read more</div>
  </div>

  <h2 class="news-title">News</h2>
  <div class="pager">
    <span><svg width="5" height="8" viewBox="0 0 5 8"><path d="M4 0.5 1 4l3 3.5" fill="none" stroke="#999"/></svg></span>
    <span><svg width="5" height="8" viewBox="0 0 5 8"><path d="M1 0.5 4 4 1 7.5" fill="none" stroke="#999"/></svg></span>
  </div>
  <section class="news">
    <article class="card"><div class="date">Sep<b>02</b></div><h3>Donec dolor tortor, aliquam quis nulla nec, elementum finibus</h3><p>Phasellus nec sapien vitae nulla bibendum commodo. Morbi suscipit molestie dolor non aliquam. Donec id fringilla tortor. Praesent in feugiat ligula, sit amet commodo risus.</p></article>
    <article class="card"><div class="date">Sep<b>02</b></div><h3>Donec dolor tortor, aliquam quis nulla nec, elementum finibus</h3><p>Phasellus nec sapien vitae nulla bibendum commodo. Morbi suscipit molestie dolor non aliquam. Donec id fringilla tortor. Praesent in feugiat ligula, sit amet commodo risus.</p></article>
    <article class="card"><div class="date">Sep<b>02</b></div><h3>Donec dolor tortor, aliquam quis nulla nec, elementum finibus</h3><p>Phasellus nec sapien vitae nulla bibendum commodo. Morbi suscipit molestie dolor non aliquam. Donec id fringilla tortor. Praesent in feugiat ligula, sit amet commodo risus.</p></article>
  </section>
</div>

<footer class="footer">
  <div class="fcol" style="left:91px"><h4>Links</h4>
    <ul><li>Home</li><li>Products</li><li>Support</li><li>Where to buy</li><li>Register your Warranty</li></ul></div>
  <div class="fcol" style="left:200px;top:44px">
    <ul><li>About</li><li>Contact</li><li>Terms and Conditions</li><li>Privacy Policy</li></ul></div>
  <div class="vline" style="left:301px"></div>
  <div class="fcol support" style="left:323px"><h4>Support</h4>
    <ul><li>Email : info@forvane.com</li><li>Live Contact with us</li><li>FAQ</li></ul></div>
  <div class="vline" style="left:442px"></div>
  <div class="fcol" style="left:466px"><h4>Newsletter Subscribe</h4>
    <div class="subscribe"><span>Email Address</span><b><svg width="8" height="6" viewBox="0 0 8 6"><rect x=".5" y=".5" width="7" height="5" fill="none" stroke="#fff"/><path d="M.5.5 4 3.5 7.5.5" fill="none" stroke="#fff"/></svg></b></div></div>
  <div class="vline" style="left:641px"></div>
  <div class="fcol" style="left:664px"><h4>Connect with us</h4>
    <div class="social">
      <span style="background:#3b5998"></span><span style="background:#1da1f2"></span><span style="background:#0a77b5"></span>
      <span style="background:#dd4b39"></span><span style="background:#cb2027"></span><span style="background:#e52d27"></span>
      <span style="background:#4a7ca6"></span><span style="background:#5aa846"></span>
    </div></div>
</footer>
<div class="bottom">Copyright © 2016 Forvane. &nbsp;All rights reserved.</div>
</body>
</html>
```